Yoga Workshop - Yoga Practice information flyer

I am a yoga teacher who will be presenting a workshop on yoga for sleep and need a brochure for my clients which outlines a practice that I give them so they can do the practice at home. Ideally I would like a brochure that is a single A3 size of paper in size that folds in half to an A4 booklet with the entire practice on the centre section to make it easy for people to do the practice at home with just one open page in front of them:
* Front page detailing "Yoga for Sleep Workshop" and "Restorative Yoga Practice"
* Centre contains the information on the practice contained in the attached word document. The practice consists of 5 postures, so there needs to be five separate sections which have the pictures of the postures (attached in uploaded files) and the wording contained in the attached word document. All pictures uploaded need to be included in the flyer as each posture has different pictures demonstrating the posture using yoga props or using things people have at home
* Back page containing a picture of myself (picture uploaded in files) with some information about me (contained in the attached word document) and my website www.calmdrift.com.au

I also need this flyer to be able to printed on 2 double sided A4 sheets of paper so will require 2 x pdf file versions. Importantly, for the centre section of the flyer, the design needs to ensure if it is printed on A4 paper, the wording and pictures for each of the postures are not separated over two pages

Target Market(s)

Existing clients

Requirements
Must have
• Detailed in project description
Nice to have
• The word document also contains some quotes. These do not need to be included in the flyer. If there is room and there is room for one or two of those please include where it would look good
Should not have
• Stock pictures of people in yoga postures which a normal everyday person could not get into

```html
<!DOCTYPE html>
<html lang="en">
<head>
<meta charset="utf-8">
<title>Yoga for Sleep Workshop – Restorative Yoga Practice</title>
<link href="https://fonts.googleapis.com/css2?family=Alegreya:wght@700&family=Barlow+Semi+Condensed:wght@500;600;700&family=Open+Sans:wght@400;600&display=swap" rel="stylesheet">
<style>
:root{
  --stage:#bdbdbd;
  --terracotta:#c07856;
  --terracotta-light:#d39a7c;
  --navy:#2d3e58;
  --accent:#c9815a;
  --peach:#fde2d4;
  --paper:#ffffff;
  --ink:#2f3640;
  --quote-mark:#d9a489;
}
*{margin:0;padding:0;box-sizing:border-box}
html,body{width:814px;height:1200px;overflow:hidden;background:var(--stage)}
body{position:relative;font-family:"Open Sans",Arial,sans-serif;color:var(--ink)}

/* ---------- Cover spread ---------- */
.cover-spread{position:absolute;left:41px;top:53px;width:731px;height:517px;overflow:hidden;background:var(--paper)}
.cover-spread svg{position:absolute;left:0;top:0}
.about-title{position:absolute;left:55px;top:45px;font-family:"Barlow Semi Condensed",sans-serif;font-weight:700;font-size:15px;color:#fff;letter-spacing:.2px}
.about-text{position:absolute;left:55px;top:68px;width:256px;font-size:5.5px;line-height:7.4px;color:#fff;text-align:justify}
.quote{position:absolute;left:55px;width:260px;padding-left:28px;font-size:5.5px;line-height:7.4px;color:#fff}
.quote::before{content:"\201C";position:absolute;left:0;top:-6px;font-family:Georgia,serif;font-size:34px;line-height:34px;color:var(--quote-mark);font-weight:700}
.quote cite{display:block;font-style:normal;font-weight:600;margin-top:4px;color:#3a2a22}
.details{position:absolute;right:382px;top:458px;text-align:right;color:#fff;font-family:"Barlow Semi Condensed",sans-serif}
.details .lead{font-size:11px;font-weight:500;line-height:13px}
.details .visit{font-size:11px;font-weight:700;color:var(--accent);line-height:14px;letter-spacing:.3px}
.details .url{font-family:"Open Sans",sans-serif;font-size:6.5px;line-height:10px}
.brand{position:absolute;left:370px;top:62px;width:190px;text-align:center}
.brand-name{display:inline-flex;align-items:center;gap:5px;font-family:"Alegreya",serif;font-weight:700;font-size:17px;color:var(--navy)}
.brand-name::before{content:"";width:9px;height:9px;border-radius:50%;background:var(--accent)}
.tagline{font-size:6px;letter-spacing:.9px;color:var(--navy);margin-top:4px}
.cover-title{position:absolute;left:400px;width:300px;top:440px;text-align:center;font-family:"Alegreya",serif;font-weight:700;line-height:28px}
.cover-title .line-1{display:block;font-size:21px;color:#fff}
.cover-title .line-2{display:block;font-size:21px;color:var(--accent)}

/* ---------- Inside pages ---------- */
.page{position:absolute;top:615px;width:353px;height:519px;background:var(--paper)}
.page-left{left:41px}
.page-right{left:420px}
.sequence-title{position:absolute;left:23px;top:16px;font-family:"Barlow Semi Condensed",sans-serif;font-weight:700;font-size:12.2px;color:var(--navy)}
.intro{position:absolute;left:23px;width:307px;font-size:5.5px;line-height:7.4px}
.posture{position:absolute;left:22px;width:307px;background:var(--peach);border-radius:6px}
.posture > *{position:absolute}
.tag{height:14px;padding:0 5px;background:var(--terracotta);color:#fff;border-radius:0 7px 7px 0;font-family:"Barlow Semi Condensed",sans-serif;font-weight:700;font-size:9.5px;line-height:14px}
.pose-name{font-family:"Barlow Semi Condensed",sans-serif;font-weight:600;font-size:8.8px;line-height:10.5px;color:var(--navy)}
.note{font-size:5px;line-height:6.6px;text-align:justify}
.note b{font-family:"Barlow Semi Condensed",sans-serif;font-weight:700;font-size:7.2px;color:var(--navy);letter-spacing:.2px}
.photo{border-radius:2px;background:linear-gradient(180deg,#9a3a3e 0%,#7c6aa8 45%,#2c8dc3 100%)}
.photo.mat{background:linear-gradient(180deg,#f2c9a6 0%,#a23a40 30%,#6d5f9e 60%,#2a8cc4 100%)}
</style>
</head>
<body>

<!-- Cover spread: back cover (left) and front cover (right) -->
<section class="cover-spread">
  <svg width="731" height="517" viewBox="0 0 731 517" aria-hidden="false">
    <defs>
      <linearGradient id="sky" x1="0" y1="0" x2="1" y2="1">
        <stop offset="0" stop-color="#ffffff"/>
        <stop offset=".45" stop-color="#dce9f3"/>
        <stop offset="1" stop-color="#b9d2e6"/>
      </linearGradient>
      <radialGradient id="warm" cx=".9" cy=".05" r=".5">
        <stop offset="0" stop-color="#f4b883" stop-opacity=".9"/>
        <stop offset="1" stop-color="#f4b883" stop-opacity="0"/>
      </radialGradient>
      <linearGradient id="rust" x1="0" y1="0" x2="1" y2="1">
        <stop offset="0" stop-color="#c27b58"/>
        <stop offset="1" stop-color="#b06a48"/>
      </linearGradient>
      <linearGradient id="seatedPhoto" x1="0" y1="0" x2="0" y2="1">
        <stop offset="0" stop-color="#b9cf9a"/>
        <stop offset=".35" stop-color="#5d82b2"/>
        <stop offset=".7" stop-color="#2a2a2e"/>
        <stop offset="1" stop-color="#e7e1d6"/>
      </linearGradient>
      <linearGradient id="reclinePhoto" x1="0" y1="0" x2="0" y2="1">
        <stop offset="0" stop-color="#8a4a2c"/>
        <stop offset=".35" stop-color="#a33a42"/>
        <stop offset=".7" stop-color="#6b5fa5"/>
        <stop offset="1" stop-color="#d7762e"/>
      </linearGradient>
    </defs>
    <!-- back cover background -->
    <rect x="0" y="0" width="366" height="517" fill="url(#rust)"/>
    <!-- front cover background -->
    <rect x="366" y="0" width="365" height="517" fill="url(#sky)"/>
    <rect x="366" y="0" width="365" height="517" fill="url(#warm)"/>
    <!-- reclining photo frame -->
    <path d="M0,396 Q60,330 114,310 Q205,385 268,517 L0,517 Z" fill="none" stroke="var(--terracotta-light)" stroke-width="3"/>
    <path role="img" aria-label="Photo of the teacher resting on her back on a yoga mat with a bolster under her knees" d="M0,398 Q60,334 114,314 Q200,388 262,517 L0,517 Z" fill="url(#reclinePhoto)"/>
    <!-- navy sweep -->
    <path d="M240,517 C280,430 330,365 420,330 C520,300 620,298 731,300 L731,517 Z" fill="var(--navy)"/>
    <path d="M420,330 C520,300 620,298 731,296" fill="none" stroke="var(--terracotta)" stroke-width="4"/>
    <!-- seated photo frame -->
    <path d="M551,108 C470,170 405,280 414,370" fill="none" stroke="var(--terracotta)" stroke-width="4"/>
    <path role="img" aria-label="Photo of the teacher sitting cross-legged in meditation outdoors, wearing a denim jacket" d="M551,114 C474,176 412,282 420,372 Q470,428 565,426 Q665,420 731,372 L731,100 C690,95 650,110 620,140 C600,135 575,125 551,114 Z" fill="url(#seatedPhoto)"/>
  </svg>

  <h2 class="about-title">ABOUT THE TEACHER...</h2>
  <p class="about-text">Natalie Verran is a current serving Navy Officer, Yoga Therapist (C-YTA) and RestWell Level 2 instructor. Natalie's classes are about using the practices and teaching of Yoga to come to the essence of your true self and learning to tap into the internal wisdom which is always present. Natalie is dedicated to making the resilience developing practices of Yoga accessible to all Australian Military personnel and their families.</p>

  <blockquote class="quote" style="top:122px">“Posture should be steady and comfortable”<cite>—Sutras of Stillness</cite></blockquote>
  <blockquote class="quote" style="top:164px">“Tension is who you think you are, Relaxation is who you actually are”</blockquote>
  <blockquote class="quote" style="top:197px">“Life isn't as serious as the mind makes it out to be”<cite style="margin-top:2px">—Elias Marrow</cite></blockquote>
  <blockquote class="quote" style="top:237px">“Watch your thoughts, they become words<br>Watch your words, they become actions<br>Watch your actions, they become habits<br>Watch your habits, they become character<br>Watch your character, for it becomes your destiny”<cite>—Upanishads</cite></blockquote>

  <div class="details">
    <p class="lead">For more details</p>
    <p class="visit">VISIT US ON</p>
    <p class="url">www.<b>calmdrift</b>.com.au</p>
  </div>

  <div class="brand">
    <p class="brand-name">Calm Drift</p>
    <p class="tagline">Be the change you wish to see in the world</p>
  </div>

  <h1 class="cover-title"><span class="line-1">Yoga for Sleep Workshop and</span><span class="line-2">Restorative Yoga Practice</span></h1>
</section>

<!-- Inside left page -->
<section class="page page-left">
  <h2 class="sequence-title">Yoga for Sleep Workshop Restorative Yoga Sleep Sequence</h2>
  <p class="intro" style="top:40px">Use this sequence to relax and unwind at the end of a day or before bed. Settle comfortably into each posture for about 5-7 minutes. Set a timer to let you know when it is time to change position, and you can also listen to any music you find relaxing at the same time. The audio recording from the Yoga for Sleep Workshop can also be used to recreate the practice at home.</p>
  <p class="intro" style="top:78px">In the middle of the night when you can't sleep, you might like to try getting up and resting in any one of these postures for about 5-10 minutes before heading back to bed.</p>

  <article class="posture" style="left:23px;top:112px;height:178px">
    <span class="tag" style="left:12px;top:11px">POSTURE 1 –</span>
    <h3 class="pose-name" style="left:12px;top:35px;width:120px">Supported Chest Opening with Knee Support</h3>
    <p class="note" style="left:12px;top:59px;width:116px"><b>PROPS –</b> 2 x bolsters (or towels rolled up lengthways), 1 x cushion for head support (optional)</p>
    <p class="note" style="left:12px;top:85px;width:116px"><b>SET UP NOTES –</b> Position the props in a T-position with one bolster/towel running parallel to the yoga mat and one bolster towel running horizontal to the mat underneath the knees. Position yourself so your buttocks is on the floor and the parallel bolster runs from the lower back up to behind the head.</p>
    <div class="photo mat" role="img" aria-label="Photo of the posture lying on a chest-opening bolster with a rolled towel under the knees" style="left:140px;top:10px;width:75px;height:130px"></div>
    <div class="photo mat" role="img" aria-label="Photo of the props arranged in a T-position on the yoga mat" style="left:235px;top:12px;width:50px;height:128px"></div>
    <p class="note" style="left:12px;top:146px;width:283px"><b>CAUTION –</b> If any lower back pain is experience adjust the parallel bolster height by using a towel. If using a towel, the height of the parallel support prop can be adjusted by either using a thinner towel or loosely rolling the towel. Do not us any parallel support prop if pain continues.</p>
  </article>

  <article class="posture" style="left:23px;top:309px;height:191px">
    <div class="photo mat" role="img" aria-label="Photo of supported bound-angle pose with pillows under the knees" style="left:3px;top:28px;width:85px;height:118px"></div>
    <div class="photo mat" role="img" aria-label="Photo of supported bound-angle pose with yoga blocks under the knees" style="left:97px;top:26px;width:72px;height:122px"></div>
    <span class="tag" style="left:176px;top:9px">POSTURE 2 –</span>
    <h3 class="pose-name" style="left:176px;top:33px;width:120px">Supported Bound-Angle Pose</h3>
    <p class="note" style="left:176px;top:47px;width:117px"><b>PROPS –</b> 1 x bolsters (or towel rolled up lengthways), 2 x yoga blocks/bolsters (or pillows), 1 x cushion for head support (optional)</p>
    <p class="note" style="left:176px;top:82px;width:117px"><b>SET UP NOTES –</b><br>Similar to Posture 1 without the bolster behind the knees. Instead, the soles of the feet are together with knees wide being supported by either blocks, bolsters or pillows.</p>
    <p class="note" style="left:176px;top:130px;width:117px"><b>CAUTION –</b><br>If any lower back pain is experience adjust the parallel bolster height by using a towel. If using a towel, the height of the parallel support prop can be adjusted by either using a thinner towel or loosely rolling the towel. Do not us any parallel support prop if pain continues.</p>
  </article>
</section>

<!-- Inside right page -->
<section class="page page-right">
  <article class="posture" style="top:18px;height:180px">
    <span class="tag" style="left:12px;top:6px">POSTURE 3 –</span>
    <h3 class="pose-name" style="left:12px;top:30px;width:125px">Elevated Legs-Up-the-Wall Pose</h3>
    <p class="note" style="left:12px;top:42px;width:117px"><b>PROPS –</b> 1 x bolsters (or towel or blanket densely folded to a width of about 15-30cm), 1 x cushion for head support (optional)</p>
    <p class="note" style="left:12px;top:75px;width:117px"><b>SET UP NOTES –</b> To enter the posture sit at 90 degrees to the wall with the side of your hip about a hand width away from the wall, and the bolster/folded towel or blanket close by. Lie down on the mat on your side then roll onto your back and extend feet up wall. The feet can push into the wall to elevate the hips slightly so the bolster/folded towel or blanket can slide underneath the hips. The prop should be positioned underneath the sacrum (flat bony structure at the base of the spine).</p>
    <div class="photo" role="img" aria-label="Photo of legs-up-the-wall pose with a folded towel under the hips" style="left:135px;top:10px;width:78px;height:137px"></div>
    <div class="photo" role="img" aria-label="Photo of legs-up-the-wall pose with a bolster under the hips" style="left:222px;top:10px;width:80px;height:137px"></div>
    <p class="note" style="left:12px;top:158px;width:284px"><b>CAUTION –</b> If any lower back pain is experience adjust the height the hips are elevated by using a towel or blanket that is folded to a lower height.</p>
  </article>

  <article class="posture" style="top:212px;height:138px">
    <div class="photo mat" role="img" aria-label="Photo of supported child's pose over a bolster, seen from above" style="left:8px;top:18px;width:62px;height:88px"></div>
    <div class="photo mat" role="img" aria-label="Photo of supported child's pose over stacked bed pillows" style="left:82px;top:18px;width:90px;height:88px"></div>
    <span class="tag" style="left:182px;top:7px">POSTURE 4 –</span>
    <h3 class="pose-name" style="left:182px;top:30px;width:115px">Supported Child's Pose</h3>
    <p class="note" style="left:182px;top:42px;width:114px"><b>PROPS –</b> 1-2 x bolsters (or 3-4 bed pillows)</p>
    <p class="note" style="left:182px;top:57px;width:114px"><b>SET UP NOTES –</b> Position bolster or stacked pillows under torso. Rest the head in one direction and remember to turn to the head to the other side half way through the time you spend in this posture.</p>
    <p class="note" style="left:182px;top:101px;width:114px"><b>CAUTION –</b> If any knee or hip pain is experience, increase the height of the support under the torso by adding more bolsters, folded blankets or pillows.</p>
  </article>

  <article class="posture" style="top:363px;height:136px">
    <span class="tag" style="left:12px;top:8px">POSTURE 5 –</span>
    <h3 class="pose-name" style="left:12px;top:31px;width:125px">Basic Relaxation Posture with Knee Support</h3>
    <p class="note" style="left:12px;top:55px;width:117px"><b>PROPS –</b> 1x bolsters (or 1 x bed pillows or rolled up towel)</p>
    <p class="note" style="left:12px;top:84px;width:117px"><b>SET UP NOTES –</b> Reclining on back, position bolster or pillows under knees.</p>
    <div class="photo mat" role="img" aria-label="Photo of relaxation pose lying on the back with a bolster under the knees" style="left:149px;top:8px;width:70px;height:118px"></div>
    <div class="photo mat" role="img" aria-label="Photo of relaxation pose lying on the back with pillows under the knees" style="left:232px;top:8px;width:70px;height:118px"></div>
  </article>
</section>

</body>
</html>
```